I need email signatures for my admin staff members
info:
Teresa Volkaric
Support Coordinator
Unit 4, 517 Marden Vale Road, Quillby NSW 2185
Tel: 02 94637215 Mob: 0417582946
email: teresa.vo@kindwayservices.com
www.kindwayservices.com

Target Market(s)

community services industry

Industry/Entity Type

Community Service

Requirements
Must have
• Specialist Provider of Multicultural Support Services
Nice to have
• "I acknowledge the traditional owners of the land on which we live, work and dream"
plus their flags as attached

```html
<!DOCTYPE html>
<html lang="en">
<head>
<meta charset="utf-8">
<title>Email Signature – Teresa Volkaric</title>
<link href="https://fonts.googleapis.com/css2?family=Lato:wght@400;700&display=swap" rel="stylesheet">
<style>
  :root {
    --orange: #f7931e;
    --ink: #333333;
    --rule: #3a3a3a;
    --paper: #ffffff;
    --social: #c9c9c9;
    --flag-dark: #1a1a1a;
    --flag-red: #d8141c;
    --flag-green: #2cc43a;
    --flag-blue: #2346d8;
  }
  * { margin: 0; padding: 0; box-sizing: border-box; }
  html, body {
    width: 1200px; height: 794px; overflow: hidden;
    background: var(--paper);
    font-family: 'Lato', sans-serif;
    color: var(--ink);
  }
  .signature {
    position: absolute; left: 0; top: 171px;
    width: 1200px; height: 451px;
    background: var(--paper);
  }
  .signature > * { position: absolute; }
  .person-name {
    left: 48px; top: 40px;
    font-size: 38px; font-weight: 700; color: var(--orange);
    line-height: 1;
  }
  .person-role {
    left: 48px; top: 89px;
    font-size: 29px; font-weight: 400; line-height: 1;
  }
  .social-links { left: 1013px; top: 51px; display: flex; gap: 4px; }
  .social-links span {
    width: 36px; height: 36px; border-radius: 50%;
    background: var(--social); display: block;
  }
  .brand { left: 82px; top: 150px; width: 300px; text-align: center; }
  .brand-mark {
    width: 112px; height: 112px; border-radius: 50%;
    background: var(--orange); margin: 0 auto 14px;
  }
  .brand-name {
    font-size: 29px; font-weight: 700; color: var(--orange);
    letter-spacing: 1px; line-height: 1; white-space: nowrap;
  }
  .tagline {
    left: 42px; top: 347px; width: 400px; text-align: center;
    font-size: 25px; line-height: 31px; color: var(--orange);
  }
  .divider {
    left: 442px; top: 160px; width: 2px; height: 151px;
    background: var(--rule);
  }
  .contact-row {
    display: flex; align-items: center; gap: 10px;
    font-size: 30px; line-height: 1; white-space: nowrap;
  }
  .contact-row svg { width: 30px; height: 30px; flex: none; }
  .row-phones { left: 486px; top: 157px; }
  .row-phones .mobile { margin-left: 20px; }
  .row-email { left: 486px; top: 194px; }
  .row-web { left: 486px; top: 230px; }
  .address {
    left: 480px; top: 281px; font-size: 30px; line-height: 1; white-space: nowrap;
  }
  .acknowledgement {
    left: 462px; top: 345px; width: 500px;
    font-size: 25px; line-height: 31px;
  }
  .flag-area { left: 979px; top: 351px; display: flex; gap: 3px; }
  .flag-area div { width: 81px; height: 54px; }
  .flag-area .first { background: linear-gradient(to bottom, var(--flag-dark), var(--flag-red)); }
  .flag-area .second { background: linear-gradient(to bottom, var(--flag-green), var(--flag-blue) 30%, var(--flag-blue) 70%, var(--flag-green)); }
</style>
</head>
<body>
  <main class="signature">
    <h1 class="person-name">Teresa Volkaric</h1>
    <p class="person-role">Support Coordinator</p>

    <div class="social-links" aria-label="Social media links">
      <span></span><span></span><span></span>
    </div>

    <div class="brand">
      <div class="brand-mark"></div>
      <div class="brand-name">KINDWAY SERVICES</div>
    </div>

    <p class="tagline">Specialist Provider of&nbsp; Multicultural<br>Support Services</p>

    <div class="divider"></div>

    <div class="contact-row row-phones">
      <svg viewBox="0 0 30 30" aria-hidden="true">
        <path fill="var(--orange)" d="M2 11c0-5 26-5 26 0v3h-6v-3c-3-1-11-1-14 0v3H2z"/>
        <path fill="var(--orange)" d="M8 14l3-3h8l3 3 3 12H5z"/>
        <g fill="var(--paper)">
          <rect x="11" y="16" width="2" height="2"/><rect x="14" y="16" width="2" height="2"/><rect x="17" y="16" width="2" height="2"/>
          <rect x="11" y="19" width="2" height="2"/><rect x="14" y="19" width="2" height="2"/><rect x="17" y="19" width="2" height="2"/>
        </g>
      </svg>
      <span>02 94637215</span>
      <svg class="mobile" viewBox="0 0 30 30" aria-hidden="true">
        <rect x="7" y="2" width="16" height="26" rx="3" fill="var(--orange)"/>
        <rect x="10" y="6" width="10" height="16" fill="var(--paper)"/>
        <circle cx="15" cy="25" r="1.3" fill="var(--paper)"/>
      </svg>
      <span>0417582946</span>
    </div>

    <div class="contact-row row-email">
      <svg viewBox="0 0 30 30" aria-hidden="true">
        <rect x="1" y="6" width="28" height="19" fill="var(--orange)"/>
        <path d="M2 7l13 10 13-10M2 24l10-9M28 24l-10-9" stroke="var(--paper)" stroke-width="1.6" fill="none"/>
      </svg>
      <span>teresa.vo@kindwayservices.com</span>
    </div>

    <div class="contact-row row-web">
      <svg viewBox="0 0 30 30" aria-hidden="true">
        <circle cx="15" cy="15" r="13" fill="var(--orange)"/>
        <path d="M4 15h22M15 2c-6 7-6 19 0 26M15 2c6 7 6 19 0 26" stroke="var(--paper)" stroke-width="1.6" fill="none"/>
      </svg>
      <span>www.kindwayservices.com</span>
    </div>

    <p class="address">Unit 4, 517 Marden Vale Road, Quillby NSW 2185</p>

    <p class="acknowledgement">“I acknowledge the traditional owners of the land on&nbsp; which we live, work and dream”</p>

    <div class="flag-area">
      <div class="first" role="img" aria-label="Aboriginal flag"></div>
      <div class="second" role="img" aria-label="Torres Strait Islander flag"></div>
    </div>
  </main>
</body>
</html>
```